All-Natural Head Lice Removal company

I need a business card with my pre-existing logo. We are a new company located in Portland Oregon that goes into peoples homes to help with head lice removal. My products and approach are all- natural and also will be around children.On my current logo we used Teal Bl and the color Green. I am open to new ideas just want it simple and creative

Target Market(s)

my biggest market is families of school aged children

Industry/Entity Type

Business

Contact Information for Business Card

see upload for details from previous business card

Font styles to use
Serif

Colors
33a6d7
9bcb3b
f37122

Requirements
Must have
• Basic information/ logo put into a creative format that is catching to the eye
Nice to have
• creative

```html
<!DOCTYPE html>
<html lang="en">
<head>
<meta charset="utf-8">
<title>Clearwell Business Card</title>
<link rel="stylesheet" href="https://fonts.googleapis.com/css2?family=Comic+Neue:wght@400;700&display=swap">
<style>
  :root {
    --page-bg: #9b9c9c;
    --card-white: #f4f5f6;
    --brand-blue: #33a6d7;
    --band-blue: #3a9fd2;
    --brand-green: #7fbf3a;
    --ink: #3c3c40;
    --headline-fill: #f7f7f7;
    --headline-edge: #6b6f72;
    --photo-light: #c9d3d6;
    --photo-mid: #9fb2b7;
    --photo-dark: #6f8489;
  }
  * { margin: 0; padding: 0; box-sizing: border-box; }
  html, body { width: 1105px; height: 1200px; overflow: hidden; }
  body {
    background: var(--page-bg);
    font-family: "Comic Neue", "Comic Sans MS", cursive;
    position: relative;
  }
  .card {
    position: absolute;
    left: 182px;
    width: 748px;
    height: 427px;
    overflow: hidden;
    box-shadow: 0 14px 22px rgba(0,0,0,.28);
  }
  .card-front { top: 119px; background: var(--card-white); }
  .card-back { top: 637px; background: var(--card-white); }

  /* front */
  .brand-mark {
    position: absolute;
    left: 92px; top: 100px;
    display: flex; align-items: center; gap: 14px;
  }
  .brand-dot {
    width: 62px; height: 62px; border-radius: 50%;
    background: var(--brand-green);
  }
  .brand-name {
    font-weight: 700; font-size: 44px; color: var(--ink);
  }
  .contact-block { position: absolute; left: 357px; top: 103px; }
  .person-name { font-size: 29px; font-weight: 700; color: var(--brand-blue); letter-spacing: .5px; }
  .person-role { font-size: 21px; color: var(--brand-green); margin-top: 2px; }
  .contact-list { list-style: none; margin-top: 14px; }
  .contact-list li {
    display: flex; align-items: center; gap: 12px;
    font-size: 22px; color: var(--ink); line-height: 29px;
  }
  .contact-list svg { width: 18px; height: 18px; flex: none; fill: var(--brand-blue); }
  .front-wave { position: absolute; left: 0; bottom: 0; width: 748px; height: 130px; }
  .front-tagline {
    position: absolute; left: 0; right: 0; bottom: 12px;
    text-align: center; color: #fff; font-size: 22px;
  }

  /* back */
  .photo-area {
    position: absolute; left: 0; top: 0; width: 748px; height: 349px;
    background: linear-gradient(100deg, var(--photo-mid) 0%, var(--photo-light) 45%, var(--photo-dark) 100%);
  }
  .headline {
    position: absolute; left: 26px; top: 14px;
    font-weight: 700; color: var(--headline-fill); line-height: .95;
    -webkit-text-stroke: 2px var(--headline-edge);
    letter-spacing: 2px;
  }
  .headline .line-one { display: block; font-size: 74px; }
  .headline .line-two { display: block; font-size: 58px; margin-left: 30px; transform: rotate(-2deg); }
  .back-band {
    position: absolute; left: 0; bottom: 0; width: 748px; height: 78px;
    background: var(--band-blue);
  }
  .back-brand {
    position: absolute; left: 28px; bottom: 24px;
    display: flex; align-items: center; gap: 8px;
  }
  .back-brand .brand-dot { width: 40px; height: 40px; }
  .back-brand .brand-name { font-size: 28px; }
  .back-copy {
    position: absolute; left: 170px; right: 0; bottom: 9px;
    text-align: center; color: #fff; font-size: 21px; line-height: 27px;
  }
</style>
</head>
<body>

<section class="card card-front">
  <div class="brand-mark">
    <span class="brand-dot"></span>
    <span class="brand-name">Clearwell</span>
  </div>

  <div class="contact-block">
    <div class="person-name">Maren Holloway</div>
    <div class="person-role">Owner</div>
    <ul class="contact-list">
      <li><svg viewBox="0 0 24 24"><path d="M6.6 10.8a15.1 15.1 0 0 0 6.6 6.6l2.2-2.2c.3-.3.7-.4 1-.2 1.1.4 2.3.6 3.6.6.6 0 1 .4 1 1V20c0 .6-.4 1-1 1A17 17 0 0 1 3 4c0-.6.4-1 1-1h3.5c.6 0 1 .4 1 1 0 1.3.2 2.5.6 3.6.1.3 0 .7-.2 1z"/></svg>1-855-555-0142</li>
      <li><svg viewBox="0 0 24 24"><path d="M2 5h20v14H2z M2 5l10 8 10-8" fill="none" stroke="#33a6d7" stroke-width="0"/><path d="M2 6.5V19h20V6.5l-10 7.5z"/><path d="M2.5 5h19L12 12.2z"/></svg>maren@clearwellhome.com</li>
      <li><svg viewBox="0 0 24 24"><path d="M12 2a10 10 0 1 0 0 20 10 10 0 0 0 0-20zm-1 17.9A8 8 0 0 1 4.1 11L9 16v1c0 1.1.9 2 2 2zm6.9-2.5A2 2 0 0 0 16 16h-1v-3c0-.6-.4-1-1-1H8v-2h2c.6 0 1-.4 1-1V7h2c1.1 0 2-.9 2-2v-.4a8 8 0 0 1 2.9 12.8z"/></svg>www.clearwellhome.com</li>
    </ul>
  </div>

  <svg class="front-wave" viewBox="0 0 748 130" preserveAspectRatio="none" aria-hidden="true">
    <path d="M0 20 Q374 70 748 22 L748 130 L0 130 Z" fill="#7fbf3a"/>
    <path d="M0 34 Q374 72 748 32 L748 130 L0 130 Z" fill="#ffffff"/>
    <path d="M0 42 Q374 78 748 38 L748 130 L0 130 Z" fill="#3a9fd2"/>
  </svg>
  <div class="front-tagline">All Natural In-Home Lice Services</div>
</section>

<section class="card card-back">
  <div class="photo-area" role="img" aria-label="Photo of a child spraying a fluffy white dog with a shower head in a bathtub"></div>
  <h1 class="headline">
    <span class="line-one">HEAD LICE</span>
    <span class="line-two">TREATMENT</span>
  </h1>
  <div class="back-band"></div>
  <div class="back-brand">
    <span class="brand-dot"></span>
    <span class="brand-name">Clearwell</span>
  </div>
  <p class="back-copy">Try Clearwell Today and Be Lice Free Tomorrow!<br>All Natural In-Home Lice Removal Services</p>
</section>

</body>
</html>
```